Striking new Advert required for Commercial Real Estate Agency

We need a a NEW newspaper advertisement for the marketing of a large commercial property (a Backpackers lodge)

Dimensions are to be width of 101mm and height of 100mm (10cms)

Our key design statement for this advert is clean, modern and minimalist design, with accents of 'HOT PINK' colour to remove it from looking too boring, perhaps in the area of the contact icons. The heirachy of the advert is outlined in the attached ADVERTISEMENT TEXT FILE.

Our company name is THE HARBOURLINE COLLECTIVE, and we want our brand to appear professional yet classy in it's design style (sort of like an advertising or design agency)

We have two logo options below, one more square in its layout (which we prefer) and the other more rectangular, which may be better suited for the layout. We are not adverse to the logo being reversed (white text on black), along with other key element areas such as the main advert heading and the "FOR SALE" part, and think this would be a good option.
There are two photos attached to be included in the advert.

We have attached an example of an old advert that we did, which we DID NOT LIKE, and which was for a smaller width than the one we need (it is only 65% of the width of this one). WE have also atached a file showing layout of some of our competitors adverts, which we dont think are too good either.

We are really open for ideas, but have time pressures, so please come back with any questions as soon as you can, if needed.

Thank you
Updates

Thank you for the great and diverse designs. There are a few standout options, but one style that we prefer most.

Target Market(s)

We are wanting this newspaper advertisement to attract interest from real estat e developers, investors and motel/lodge owners, along with other high nett worth individuals

Industry/Entity Type

Real Estate

Font styles to use
Serif
Sans Serif

Colors
1b1b1b
a54499
474747
fbfbfb

Requirements
Must have
• Clean modern look, predominantly monochromatic or black and white, with the hot pink accent somewhere, as mentioned above.
• All the contents of the TEXT provided, perhaps with additional space to add a little more if needed, Please advise if you think we dont have enough space for all of the TEXT
Should not have
• Script like fonts
• Cartoonish characters
• a 'cheap' look

```html
<!DOCTYPE html>
<html lang="en">
<head>
<meta charset="utf-8">
<title>For Sale – Mount Victoria Land Grab</title>
<link href="https://fonts.googleapis.com/css2?family=Montserrat:wght@500;600&family=Roboto+Condensed:wght@400;700&display=swap" rel="stylesheet">
<style>
  :root {
    --backdrop: #e6e6e6;
    --paper: #ffffff;
    --ink: #1b1b1b;
    --ink-soft: #474747;
    --hot-pink: #a8207f;
    --photo-aerial: linear-gradient(160deg, #b9c0c4 0%, #8f9a8a 40%, #5f7a45 75%, #3d5a2b 100%);
    --photo-facade: linear-gradient(180deg, #6f9bd8 0%, #dfe3ea 35%, #c9cdd4 65%, #4f6a36 100%);
  }
  * { margin: 0; padding: 0; box-sizing: border-box; }
  html, body { width: 1200px; height: 1000px; overflow: hidden; }
  body { background: var(--backdrop); position: relative; font-family: "Roboto Condensed", sans-serif; color: var(--ink); }

  .advert { position: absolute; left: 160px; top: 68px; width: 880px; height: 872px; background: var(--paper); }

  .headline { position: absolute; left: 28px; top: 22px; font-family: "Montserrat", sans-serif; font-weight: 600; font-size: 66px; line-height: 1; color: var(--hot-pink); letter-spacing: 0.5px; }
  .listing-title { position: absolute; right: 25px; top: 46px; text-align: right; font-family: "Montserrat", sans-serif; color: var(--ink); }
  .listing-title__name { font-size: 19px; font-weight: 500; letter-spacing: 0.3px; line-height: 1.1; }
  .listing-title__address { font-size: 14px; font-weight: 500; margin-top: 3px; }

  .photo { position: absolute; top: 112px; height: 369px; }
  .photo--aerial { left: 0; width: 510px; background: var(--photo-aerial); }
  .photo--facade { left: 516px; width: 364px; background: var(--photo-facade); }

  .summary { position: absolute; left: 26px; top: 506px; width: 530px; font-size: 21px; line-height: 29px; color: var(--ink); }
  .summary__features { list-style: none; }
  .summary__features li { position: relative; padding-left: 18px; }
  .summary__features li::before { content: ""; position: absolute; left: 0; top: 10px; width: 9px; height: 9px; background: var(--hot-pink); }

  .sale-panel { position: absolute; left: 585px; top: 506px; width: 280px; }
  .sale-method { font-weight: 700; font-size: 21px; color: var(--hot-pink); line-height: 29px; }

  .brand { display: flex; align-items: center; gap: 16px; margin-top: 20px; height: 116px; }
  .brand__square { width: 22px; height: 22px; background: var(--ink); flex: none; }
  .brand__name { font-family: "Montserrat", sans-serif; font-weight: 500; font-size: 23px; line-height: 31px; letter-spacing: 1.5px; color: var(--ink); }

  .agent { margin-top: 8px; font-weight: 700; font-size: 20px; line-height: 27px; }
  .agent__contacts { list-style: none; margin-top: 1px; }
  .agent__contacts li { display: flex; align-items: center; gap: 6px; }
  .agent__contacts svg { width: 17px; height: 17px; flex: none; fill: none; stroke: var(--hot-pink); stroke-width: 2; }
</style>
</head>
<body>
  <article class="advert">
    <h1 class="headline">FOR SALE</h1>
    <div class="listing-title">
      <p class="listing-title__name">MOUNT VICTORIA LAND GRAB</p>
      <p class="listing-title__address">Rosalind’s Lodge, 42 Calder Street, Mount Victoria</p>
    </div>

    <div class="photo photo--aerial" role="img" aria-label="Aerial photograph of the lodge buildings, car park and surrounding Mount Victoria houses"></div>
    <div class="photo photo--facade" role="img" aria-label="Photograph of the white weatherboard lodge facade with fire escape balconies"></div>

    <section class="summary">
      <p>This Old Beauty has served many, and is now ripe for development.</p>
      <p>One of Mt Vic’s largest land areas, now offered with vacant possession, with key details being:</p>
      <ul class="summary__features">
        <li>Large Land area of 2076m² with elevated sunny position and great outlook + access from Halcombe Street</li>
        <li>Existing Backpackers Lodge of 970m² providing multiple rooms with amenity areas</li>
        <li>Four adjacent sites also available, taking total land area to 4452m², an unprecedented Land</li>
        <li>Offering in this popular cuity fringe location</li>
      </ul>
    </section>

    <aside class="sale-panel">
      <p class="sale-method">Now Selling by Closed Tender</p>
      <div class="brand">
        <span class="brand__square"></span>
        <p class="brand__name">THE<br>HARBOURLINE<br>COLLECTIVE</p>
      </div>
      <div class="agent">
        <p>Contact the Sole Agenct :</p>
        <p>Dean Marlow</p>
        <ul class="agent__contacts">
          <li><svg viewBox="0 0 24 24"><path d="M5 3h4l2 5-3 2a12 12 0 0 0 6 6l2-3 5 2v4a2 2 0 0 1-2 2A18 18 0 0 1 3 5a2 2 0 0 1 2-2z"/></svg>(04) 555 0182</li>
          <li><svg viewBox="0 0 24 24"><rect x="7" y="2" width="10" height="20" rx="2"/><line x1="11" y1="18" x2="13" y2="18"/></svg>(021) 555 736</li>
          <li><svg viewBox="0 0 24 24"><rect x="3" y="6" width="18" height="13" rx="1"/><path d="M3 7l9 7 9-7"/></svg>dean@harbourline.example</li>
          <li><svg viewBox="0 0 24 24"><circle cx="12" cy="12" r="9"/><path d="M3 12h18M12 3c3 3 3 15 0 18M12 3c-3 3-3 15 0 18"/></svg>www.harbourline.example</li>
        </ul>
      </div>
    </aside>
  </article>
</body>
</html>
```